Anzeigengestaltung für eine Hausarztpraxis
Zielgruppe
Wir sind eine Hausarztpraxis mit zwei Standorten und suchen eine Ärztin oder einen Arzt zur Anstellung in der klassischen Hausarzt Medizin am Standort Tannwil
Aufgabenstellung
Bitte beachtet den Text im Anhang, der ist schon vorgegeben. (Anzeigentext)
Wir suchen ein ruhiges, hochwertiges Layout für eine Stellenanzeige einer Hausarztpraxis in einem historischen Gebäude.
Der Text steht im Vordergrund, das Design soll zurückhaltend, klar und wertig sein.
Bitte keine Icons, keine bunten Farben, keine verspielten Elemente.
Gerne viel Weissraum, klare Typografie, ruhige Anmutung.
Schrift: Garamond für den Fliesstext (bereits gewählt).
Das Layout soll sowohl als PDF wie auch online funktionieren.
Optional: ein sehr dezentes grafisches Element oder eine ruhige Bildanmutung (z. B. Struktur, Licht, Architekturdetail).

```html
<!DOCTYPE html>
<html lang="de">
<head>
<meta charset="utf-8">
<title>Stellenanzeige Hausarztpraxis</title>
<link href="https://fonts.googleapis.com/css2?family=EB+Garamond:wght@400;600;700&display=swap" rel="stylesheet">
<style>
  :root {
    --page-bg: #d9dcdf;
    --paper: #ffffff;
    --text: #555555;
    --text-dark: #2b2b2b;
    --accent: #8cbf26;
    --footer-bg: #eff3e6;
    --band: rgba(45, 45, 45, 0.78);
  }
  * { box-sizing: border-box; margin: 0; padding: 0; }
  html, body { width: 1200px; height: 1200px; overflow: hidden; }
  body {
    background: var(--page-bg);
    font-family: "EB Garamond", Garamond, serif;
    color: var(--text);
    position: relative;
  }
  .ad {
    position: absolute;
    left: 243px; top: 90px;
    width: 714px; height: 1009px;
    background: var(--paper);
    box-shadow: 0 2px 8px rgba(0,0,0,0.18);
    overflow: hidden;
  }
  .hero {
    position: absolute; left: 0; top: 0; width: 714px; height: 259px;
    background: linear-gradient(180deg, #e9e9e7 0%, #e4e3df 55%, #8f9487 78%, #b9b2a4 100%);
  }
  .hero-band {
    position: absolute; left: 0; top: 154px; width: 625px; height: 80px;
    background: var(--band);
    padding: 8px 0 0 43px;
    color: #fff;
    white-space: nowrap;
  }
  .hero-title { font-size: 29px; font-weight: 600; line-height: 31px; }
  .hero-subtitle { font-size: 29px; font-weight: 400; line-height: 31px; }
  .intro {
    position: absolute; left: 43px; top: 292px; width: 197px; height: 218px;
    border-top: 2px solid var(--accent);
    border-bottom: 2px solid var(--accent);
    padding: 8px 0 0;
    color: var(--text-dark);
    font-size: 16px; line-height: 21.5px;
    white-space: nowrap;
  }
  .intro p + p { margin-top: 7px; }
  .body-copy {
    position: absolute; left: 277px; top: 283px; width: 392px;
    font-size: 13.8px; line-height: 18px;
  }
  .body-copy p { margin-bottom: 7px; }
  .body-copy h2 {
    font-size: 17.5px; font-weight: 600; color: var(--text-dark);
    line-height: 22px; margin: 0 0 4px;
  }
  .body-copy h2.first { margin-top: 19px; }
  .footer {
    position: absolute; left: 0; top: 841px; width: 714px; height: 168px;
    background: var(--footer-bg);
  }
  .brand {
    position: absolute; left: 51px; top: 69px;
    display: flex; align-items: center; gap: 10px;
    font-size: 17px; font-weight: 600; color: var(--text-dark);
  }
  .brand-dot { width: 12px; height: 12px; border-radius: 50%; background: var(--accent); }
  .contact {
    position: absolute; left: 277px; top: 24px;
    font-size: 13.8px; line-height: 18px;
  }
  .contact strong { color: var(--text-dark); font-weight: 700; }
  .contact .gap { margin-top: 15px; }
  .contact .gap-sm { margin-top: 5px; }
</style>
</head>
<body>
  <article class="ad">
    <header class="hero" role="img" aria-label="Fotografie: historische weisse Hausfassade mit roten Fensterläden, Holztür, Laternen und Formbäumen">
      <div class="hero-band">
        <h1 class="hero-title">Hausarztmedizin mit Tiefe</h1>
        <p class="hero-subtitle">– dort, wo man noch echte Grundversorgung lebt</p>
      </div>
    </header>

    <aside class="intro">
      <p>Ein Ort, der trägt.<br>Ein Team, das bleibt.<br>Eine Arbeit, die Wertschätzung<br>hat.</p>
      <p>Manche Orte verändern die Art,<br>wie man arbeitet.</p>
      <p>Unsere Praxis in Tannwil ist<br>so ein Ort.</p>
    </aside>

    <section class="body-copy">
      <p>In einem historischen Gebäude gelegen, mit grosszügigem Ambiente, warmen Vertäfelungen und kunstvoller Wandbemalung, entstehen hier Behandlungsräume von Ruhe und Würde. Kein steriler Praxisalltag, sondern ein Ort, der Gespräche trägt und medizinische Arbeit unterstützt.</p>
      <p>Für diesen besonderen Ort suchen wir eine Hausärztin oder einen Hausarzt, die oder der nicht einfach einen Arbeitsplatz sucht, sondern einen Platz, an dem Medizin menschlich sein darf.</p>
      <h2 class="first">Ein Team mit Haltung</h2>
      <p>Sie arbeiten in einem freundlichen, über Jahre gewachsenen Team mit hoher personeller Kontinuität und geringer Fluktuation.</p>
      <h2>Zeit für gute Medizin</h2>
      <p>Unsere Patientinnen und Patienten sind überwiegend gut bis sehr gut situiert, wertschätzend und therapieoffen. Das ermöglicht ruhiges, strukturiertes Arbeiten mit Fokus auf Qualität, Beziehung und nachhaltige Behandlung.</p>
      <h2>Und sonst?</h2>
      <p>Der Praxisalltag ist klar strukturiert, ruhig und verlässlich. Geregelte und in Abstimmung flexible Arbeitszeiten ohne Wochenend- oder Nachtdienste, eine sehr gute leistungsbezogene Vergütung sowie ein respektvoller, wertschätzender Umgang auf Augenhöhe schaffen ein Umfeld, in dem man sich auf die medizinische Arbeit konzentrieren und langfristig wohlfühlen kann.</p>
      <p>Wir freuen uns über eine unkomplizierte Kontaktaufnahme per E-Mail oder Telefon – gerne auch ganz unverbindlich und ohne vollständige Bewerbungsunterlagen.</p>
    </section>

    <footer class="footer">
      <div class="brand"><span>Arztpraxis Lindenhof</span><span class="brand-dot"></span></div>
      <div class="contact">
        <p><strong>E-Mail:</strong> Helga.Weißmoor@praxis-lindenhof.ch</p>
        <p class="gap"><strong>Arztpraxis Lindenhof</strong></p>
        <p class="gap-sm">Mühlegasse 7<br>4713 Tannwil</p>
        <p class="gap-sm">Tel: 0621234567</p>
      </div>
    </footer>
  </article>
</body>
</html>
```